Talon Microsystems PowerPoint Master Slide Deck Design

This is a 2-phase project to design a slide deck for a semiconductor company in the Silicon Valley. The design budget will be increased with each phase.
The slide deck will need to have one version with a dark background for presentations and a second version with a white background. Otherwise, the slides will be the same. I anticipate we will need a total of 10 slides, but that number may change.
The first phase will be to design a Title and a Title and Content slide.
- The Title Slide is the first slide of the deck. It should include the presentation title, the presenter's name and date of presentation
- The Title and Content slide should include a title and content with bullet points and up to 2 additional sub-bullets
- The Title and Content slide should have a footer that includes the slide #, Talon Microsystems Confidential, and the logo. This footer will be on every slide except the Title Slide
The first two slides will serve as the format for the remaining ~8 slides:
-Header and Content Text (1, 2, 4 column)
-Header and Content Image (bar chart, pie chart, tables)
-Break
-Title only
-Closing (Talon logo only)
Our slides contain a lot of content so a clean and simple design is best.
Both phases will need to include pre-set color options for
-Text and Lines
-Shadows
-Bullets and sub-bullets (including shapes, ex. circle, slash, square, etc.)
-Bar charts, pie charts, tables
Samples of our collateral are attached. Logo files are also attached
Look and feel
Each slider illustrates characteristics of the customer's brand and the style your logo design should communicate.

```html
<!DOCTYPE html>
<html lang="en">
<head>
<meta charset="utf-8">
<title>Talon Microsystems Confidential – Slide Deck</title>
<link href="https://fonts.googleapis.com/css2?family=Poppins:wght@400;500;600;700&display=swap" rel="stylesheet">
<style>
  :root {
    --ink: #1e1e24;
    --ink-soft: #3a3a44;
    --accent: #1a5cff;
    --footer-a: #0b90ff;
    --footer-b: #0a47ff;
    --night-a: #2a0f4d;
    --night-b: #2b3a8f;
    --paper: #ffffff;
    --page: #ffffff;
    --shadow: rgba(20, 30, 70, 0.18);
  }
  * { box-sizing: border-box; margin: 0; padding: 0; }
  html, body {
    width: 1200px; height: 4013px; overflow: hidden;
    background: var(--page);
    font-family: "Poppins", sans-serif;
    color: var(--ink);
  }
  .slide {
    position: absolute; left: 64px; width: 1073px; height: 602px;
    background: var(--paper);
    box-shadow: 0 2px 10px var(--shadow);
    overflow: hidden;
  }
  /* Title slide */
  .slide-title { top: 56px; background: linear-gradient(110deg, var(--night-a) 0%, #2c1a66 45%, var(--night-b) 100%); color: #fff; }
  .brand { position: absolute; display: flex; align-items: center; gap: 14px; font-weight: 600; color: #fff; }
  .brand-dot { border: 4px solid currentColor; border-radius: 50%; }
  .slide-title .brand { left: 53px; top: 120px; font-size: 34px; }
  .slide-title .brand-dot { width: 30px; height: 30px; }
  .deck-title { position: absolute; left: 53px; top: 250px; font-size: 37px; font-weight: 700; line-height: 56px; letter-spacing: 0.3px; }
  .presenter { position: absolute; left: 53px; top: 378px; font-size: 25px; font-weight: 600; }
  .deck-date { position: absolute; left: 53px; top: 430px; font-size: 24px; font-weight: 600; display: flex; align-items: center; gap: 14px; }
  .chip-art {
    position: absolute; left: 560px; top: 60px; width: 500px; height: 500px;
    background: radial-gradient(ellipse at 50% 55%, #3fe0ff 0%, #3a7cf0 25%, #5a3ac0 48%, rgba(43,58,143,0) 70%);
  }

  /* Content slides */
  .slide-heading { position: absolute; left: 53px; top: 32px; font-size: 29px; font-weight: 600; }
  .slide-heading .hl { color: var(--accent); }
  .col { position: absolute; top: 88px; width: 470px; }
  .col-left { left: 53px; }
  .col-right { left: 562px; }
  .point { position: relative; padding-left: 30px; font-size: 16.5px; line-height: 31px; color: var(--ink); }
  .point::before { content: ""; position: absolute; left: 0; top: 10px; width: 11px; height: 11px; border-radius: 50%; background: var(--ink); }
  .subs { list-style: none; margin: 14px 0 20px; }
  .subs li { position: relative; padding-left: 52px; font-size: 12.5px; line-height: 25px; color: var(--ink-soft); margin-bottom: 10px; }
  .subs li::before { content: ""; position: absolute; left: 30px; top: 9px; width: 7px; height: 7px; border-radius: 50%; background: var(--ink); }
  .link { color: var(--accent); }

  .footer {
    position: absolute; left: 0; bottom: 0; width: 100%; height: 47px;
    background: linear-gradient(180deg, var(--footer-a), var(--footer-b));
    color: #fff; font-size: 15.5px;
    display: flex; align-items: center; justify-content: space-between; padding: 0 53px;
  }
  .footer-brand { display: flex; align-items: center; gap: 6px; font-weight: 600; font-size: 15px; }
  .footer-brand .brand-dot { width: 14px; height: 14px; border-width: 2px; }

  /* Photo slide */
  .photo-frame { position: absolute; left: 602px; top: 56px; width: 405px; height: 456px; background: var(--accent); }
  .photo { position: absolute; left: 616px; top: 44px; width: 403px; height: 456px;
    background: radial-gradient(ellipse at 45% 45%, #c98a55 0%, #6a5060 25%, #24384f 55%, #13202f 100%); }

  /* Chart */
  .chart { position: absolute; left: 68px; top: 140px; width: 440px; height: 300px; }

  /* Closing */
  .slide-closing { top: 3348px; background: linear-gradient(180deg, #0b90ff 0%, #0a47ff 100%); }
  .slide-closing .brand { left: 0; right: 0; top: 255px; justify-content: center; font-size: 54px; gap: 22px; }
  .slide-closing .brand-dot { width: 50px; height: 50px; border-width: 6px; }
</style>
</head>
<body>

<section class="slide slide-title">
  <div class="brand"><span class="brand-dot"></span>Talon Microsystems</div>
  <h1 class="deck-title">TALON MICROSYSTEMS<br>CONFIDENTIAL</h1>
  <div class="presenter">Daniel</div>
  <div class="deck-date">
    <svg width="30" height="30" viewBox="0 0 30 30" fill="none" stroke="#fff" stroke-width="2"><rect x="3" y="5" width="22" height="21" rx="2"/><line x1="3" y1="11" x2="25" y2="11"/><line x1="9" y1="2" x2="9" y2="7"/><line x1="19" y1="2" x2="19" y2="7"/><circle cx="22" cy="23" r="5" fill="#2c1a66"/><path d="M22 20v3h2"/></svg>
    [13-12-2023]
  </div>
  <div class="chip-art" role="img" aria-label="Glowing isometric microchip illustration"></div>
</section>

<section class="slide" style="top:715px">
  <h2 class="slide-heading">Talon Microsystems <span class="hl">Confidential</span></h2>
  <div class="col col-left">
    <p class="point">Lorem ipsum dolor sit amet, consectetur adipiscing elit, sed do eiusmod tempor incididunt ut labore et dolore magna aliqua.</p>
    <ul class="subs">
      <li>Ut enim ad minim veniam, quis nostrud exercitation ullamco laboris nisi ut aliquip ex ea commodo consequat.</li>
      <li>Ut enim ad minim veniam, <span class="link">quis nostrud exercitation ullamco</span> laboris nisi ut aliquip ex ea commodo consequat.</li>
    </ul>
    <p class="point">Duis aute irure dolor in reprehenderit in voluptate velit esse cillum dolore eu fugiat nulla pariatur.</p>
    <ul class="subs">
      <li>But I must explain to you how all this mistaken idea of denouncing pleasure and praising pain</li>
      <li>No one rejects, dislikes, or avoids pleasure itself, because it is pleasure</li>
    </ul>
  </div>
  <div class="col col-right">
    <p class="point">Lorem ipsum dolor sit amet, consectetur adipiscing elit, sed do eiusmod tempor <span class="link">incididunt ut labore et dolore magna aliqua.</span></p>
    <ul class="subs">
      <li>Ut enim ad minim veniam, quis nostrud exercitation ullamco laboris nisi ut aliquip ex ea commodo consequat.</li>
      <li>Ut enim ad minim veniam, quis nostrud exercitation ullamco laboris nisi ut aliquip ex ea commodo consequat.</li>
    </ul>
    <p class="point">Duis aute irure dolor in reprehenderit in voluptate velit esse cillum dolore eu fugiat nulla pariatur.</p>
    <ul class="subs">
      <li>But I must explain to you how all this mistaken idea of denouncing pleasure and praising pain</li>
      <li>No one rejects, dislikes, or avoids pleasure itself, <span class="link">because it is pleasure</span></li>
    </ul>
  </div>
  <footer class="footer"><span>Talon Microsystems Confidential</span><span class="footer-brand"><span class="brand-dot"></span>TALON</span><span>Page Number :02</span></footer>
</section>

<section class="slide" style="top:1373px">
  <h2 class="slide-heading">Talon Microsystems <span class="hl">Confidential</span></h2>
  <div class="col col-left">
    <p class="point">Lorem ipsum dolor sit amet, consectetur adipiscing elit, sed do eiusmod tempor incididunt ut labore et dolore magna aliqua.</p>
    <ul class="subs">
      <li>Ut enim ad minim veniam, quis nostrud exercitation ullamco laboris nisi ut aliquip ex ea commodo consequat.</li>
      <li>Ut enim ad minim veniam, <span class="link">quis nostrud exercitation ullamco</span> laboris nisi ut aliquip ex ea commodo consequat.</li>
    </ul>
    <p class="point">Duis aute irure dolor in reprehenderit in voluptate velit esse cillum dolore eu fugiat nulla pariatur.</p>
    <ul class="subs">
      <li>But I must explain to you how all this mistaken idea of denouncing pleasure and praising pain</li>
      <li>No one rejects, dislikes, or avoids pleasure itself, because it is pleasure</li>
    </ul>
  </div>
  <div class="photo-frame"></div>
  <div class="photo" role="img" aria-label="Close-up photograph of a processor chip on a circuit board"></div>
  <footer class="footer"><span>Talon Microsystems Confidential</span><span class="footer-brand"><span class="brand-dot"></span>TALON</span><span>Page Number :03</span></footer>
</section>

<section class="slide" style="top:2031px">
  <h2 class="slide-heading">Talon Microsystems <span class="hl">Confidential</span></h2>
  <svg class="chart" viewBox="0 0 440 300" font-family="Poppins, sans-serif">
    <text x="18" y="26" font-size="21" fill="#c0283c">Lorem Ipsum</text>
    <text x="18" y="42" font-size="7.5" fill="#777">Sed ut perspiciatis unde omnis iste natus error sit voluptatem accusantium</text>
    <text x="18" y="52" font-size="7.5" fill="#777">doloremque laudantium totam rem aperiam eaque ipsa.</text>
    <path d="M40 240 C70 240 70 170 95 170 C120 170 120 240 150 240Z" fill="#1f4f86"/>
    <path d="M85 240 C115 240 115 130 140 130 C165 130 165 240 195 240Z" fill="#25a3dc"/>
    <path d="M130 240 C160 240 160 90 190 90 C220 90 220 240 250 240Z" fill="#4fd0c8"/>
    <path d="M185 240 C210 240 210 150 230 150 C250 150 250 240 275 240Z" fill="#f29a2e"/>
    <path d="M215 240 C245 240 245 110 270 110 C295 110 295 240 325 240Z" fill="#e6445a"/>
    <path d="M260 240 C290 240 290 185 310 185 C330 185 330 240 360 240Z" fill="#9b1c45"/>
    <g font-size="11" text-anchor="middle">
      <text x="95" y="162" fill="#1f4f86">15%</text>
      <text x="140" y="122" fill="#25a3dc">19%</text>
      <text x="190" y="82" fill="#4fd0c8">25%</text>
      <text x="236" y="142" fill="#f29a2e">17%</text>
      <text x="272" y="102" fill="#e6445a">23%</text>
      <text x="315" y="177" fill="#9b1c45">10%</text>
    </g>
    <line x1="30" y1="256" x2="420" y2="256" stroke="#c8ccd4" stroke-width="1.5"/>
    <circle cx="30" cy="256" r="4" fill="#c8ccd4"/><circle cx="420" cy="256" r="4" fill="#c8ccd4"/>
    <rect x="258" y="252" width="22" height="8" fill="#c0283c"/>
    <text x="269" y="270" font-size="7" text-anchor="middle" fill="#c0283c">123.58</text>
    <text x="30" y="275" font-size="13" text-anchor="middle" fill="#666">2000</text>
    <text x="420" y="275" font-size="13" text-anchor="middle" fill="#666">2020</text>
  </svg>
  <div class="col col-right">
    <p class="point">Lorem ipsum dolor sit amet, consectetur adipiscing elit, sed do eiusmod tempor <span class="link">incididunt ut labore et dolore magna aliqua.</span></p>
    <ul class="subs">
      <li>Ut enim ad minim veniam, quis nostrud exercitation ullamco laboris nisi ut aliquip ex ea commodo consequat.</li>
      <li>Ut enim ad minim veniam, quis nostrud exercitation ullamco laboris nisi ut aliquip ex ea commodo consequat.</li>
    </ul>
    <p class="point">Duis aute irure dolor in reprehenderit in voluptate velit esse cillum dolore eu fugiat nulla pariatur.</p>
    <ul class="subs">
      <li>But I must explain to you how all this mistaken idea of denouncing pleasure and praising pain</li>
      <li>No one rejects, dislikes, or avoids pleasure itself, <span class="link">because it is pleasure</span></li>
    </ul>
  </div>
  <footer class="footer"><span>Talon Microsystems Confidential</span><span class="footer-brand"><span class="brand-dot"></span>TALON</span><span>Page Number :04</span></footer>
</section>

<section class="slide" style="top:2690px">
  <h2 class="slide-heading">Talon Microsystems <span class="hl">Confidential</span></h2>
  <div class="col col-left">
    <p class="point">Lorem ipsum dolor sit amet, consectetur adipiscing elit, sed do eiusmod tempor incididunt ut labore et dolore magna aliqua.</p>
    <ul class="subs">
      <li>Ut enim ad minim veniam, quis nostrud exercitation ullamco laboris nisi ut aliquip ex ea commodo consequat.</li>
      <li>Ut enim ad minim veniam, <span class="link">quis nostrud exercitation ullamco</span> laboris nisi ut aliquip ex ea commodo consequat.</li>
    </ul>
    <p class="point">Duis aute irure dolor in reprehenderit in voluptate velit esse cillum dolore eu fugiat nulla pariatur.</p>
    <ul class="subs">
      <li>But I must explain to you how all this mistaken idea of denouncing pleasure and praising pain</li>
      <li>No one rejects, dislikes, or avoids pleasure itself, because it is pleasure</li>
    </ul>
  </div>
  <div class="col col-right">
    <p class="point">Lorem ipsum dolor sit amet, consectetur adipiscing elit, sed do eiusmod tempor <span class="link">incididunt ut labore et dolore magna aliqua.</span></p>
    <ul class="subs">
      <li>Ut enim ad minim veniam, quis nostrud exercitation ullamco laboris nisi ut aliquip ex ea commodo consequat.</li>
      <li>Ut enim ad minim veniam, quis nostrud exercitation ullamco laboris nisi ut aliquip ex ea commodo consequat.</li>
    </ul>
    <p class="point">Duis aute irure dolor in reprehenderit in voluptate velit esse cillum dolore eu fugiat nulla pariatur.</p>
    <ul class="subs">
      <li>But I must explain to you how all this mistaken idea of denouncing pleasure and praising pain</li>
      <li>No one rejects, dislikes, or avoids pleasure itself, <span class="link">because it is pleasure</span></li>
    </ul>
  </div>
  <footer class="footer"><span>Talon Microsystems Confidential</span><span class="footer-brand"><span class="brand-dot"></span>TALON</span><span>Page Number :05</span></footer>
</section>

<section class="slide slide-closing">
  <div class="brand"><span class="brand-dot"></span>Talon Microsystems</div>
</section>

</body>
</html>
```